Quillbay.vc needs a better website design!

We need a new and better website for Quillbay.vc. We're a Canadian venture capital firm that invests in innovative entrepreneurs. We compete against the following websites: tormelo.vc, brightvalefund.ca, kestrowvc.com, and dovaran.vc. We're a diverse group of partners and we're dedicated to the founders we invest in.
Updates

I don’t really like stock photos of random people as part of the website design…so please try to stay away from using those images. Thanks, Owen

Target Market(s)

Canadian entrepreneurs and investors

Industry/Entity Type

Venture capital, finance, investment, entrepreneurship

Coding

Coded - Design and coding required

Number of Pages Required

4 page

Font styles to use
Sans Serif

Colors

Designer to choose colors to be used in the design.

Requirements
Must have
• Clean crisp overall design. Fast and to the point.
Nice to have
• Check out www.quillbay.vc - I did it myself and it is too basic and too wordy.
Should not have
• No stock images with random people in them! Not too wordy or with too many large images that are slow to load.

```html
<!DOCTYPE html>
<html lang="en">
<head>
<meta charset="utf-8">
<title>Quillbay.vc</title>
<link href="https://fonts.googleapis.com/css2?family=Work+Sans:wght@400;500;600;700&display=swap" rel="stylesheet">
<style>
:root{
  --green:#7b9a2f;
  --green-dark:#556e1c;
  --green-hero:#6f8f2b;
  --ink:#1d1d1d;
  --muted:#555;
  --grey-bg:#ececec;
  --white:#fff;
  --black:#0d0d0d;
}
*{margin:0;padding:0;box-sizing:border-box}
html,body{width:1200px;height:4360px;overflow:hidden}
body{font-family:"Work Sans",Arial,sans-serif;color:var(--ink);background:var(--white);position:relative}
.abs{position:absolute}
.btn{position:absolute;background:var(--green);color:var(--white);font-weight:600;font-size:17px;padding:13px 26px;border-radius:4px}
.btn-light{background:var(--white);color:var(--ink)}
.rule{position:absolute;width:70px;height:3px;background:var(--green)}
.section-title{position:absolute;font-weight:700;font-size:30px;color:var(--ink)}
.body-copy{position:absolute;font-size:16px;line-height:30px;color:var(--muted)}
/* hero */
.hero{position:absolute;left:0;top:0;width:1200px;height:600px;background:linear-gradient(135deg,#8aa83e,#5f7e24 60%,#748f2c)}
.brand{position:absolute;display:flex;align-items:center;gap:10px;font-weight:700;font-size:24px;color:var(--white)}
.brand .dot{width:34px;height:34px;border-radius:50%;border:3px solid currentColor}
.nav{position:absolute;left:430px;top:55px;display:flex;gap:92px;font-size:16px;font-weight:600;color:var(--white)}
.hero-text{position:absolute;left:0;top:228px;width:1200px;text-align:center;color:var(--white);font-weight:700;font-size:30px;line-height:44px}
/* photos */
.photo{position:absolute;border-radius:50%;background:linear-gradient(160deg,#c9cfd6,#7d8996)}
.grey{position:absolute;left:0;width:1200px;background:var(--grey-bg)}
.logo-cell{position:absolute;font-weight:700;font-size:26px;color:#333;display:flex;align-items:center;gap:10px}
.logo-cell .sq{width:20px;height:20px;background:var(--green)}
.card{position:absolute;width:310px;height:345px;background:var(--white);border:1px solid #d6d6d6}
.card .tag{position:absolute;left:20px;top:16px;font-size:13px;color:#666}
.card h3{position:absolute;left:20px;top:44px;width:270px;font-size:21px;line-height:28px;font-weight:700}
.card .img{position:absolute;left:0;top:160px;width:310px;height:128px}
.card .more{position:absolute;left:20px;top:310px;font-size:12px;font-weight:600}
.arrow{position:absolute;font-size:40px;color:var(--green);font-weight:400}
.footer{position:absolute;left:0;top:3930px;width:1200px;height:370px;background:var(--black);color:var(--white)}
.footer h4{position:absolute;font-size:19px;font-weight:700}
.footer .line{position:absolute;font-size:14px;color:#ddd}
.social{position:absolute;width:20px;height:20px;border-radius:50%;background:var(--green)}
.copy-bar{position:absolute;left:0;top:4300px;width:1200px;height:60px;background:#1a1a1a;color:#bbb;font-size:13px}
</style>
</head>
<body>

<!-- Hero -->
<header class="hero" role="img" aria-label="Office workspace background in green tint">
  <div class="brand" style="left:40px;top:36px"><span class="dot"></span>Quillbay.vc</div>
  <nav class="nav"><span>Home</span><span>What</span><span>How</span><span>Who</span><span>Portfolio</span></nav>
  <svg class="abs" style="left:1060px;top:52px" width="24" height="24" viewBox="0 0 24 24"><circle cx="10" cy="10" r="7" fill="none" stroke="#fff" stroke-width="2.5"/><line x1="15" y1="15" x2="22" y2="22" stroke="#fff" stroke-width="2.5"/></svg>
  <p class="hero-text">Quillbay.vc is a venture capital firm that invests<br>in innovative seed-stage<br>technology companies in Western Canada<br>focused on B2B and SaaS markets.</p>
  <span class="btn btn-light" style="left:522px;top:405px">Get Started</span>
</header>

<!-- How we invest -->
<section>
  <div class="abs" style="left:130px;top:860px;width:150px;height:150px;border-radius:50%;background:var(--green)"></div>
  <div class="abs" style="left:195px;top:660px;width:300px;height:300px;border-radius:50%;border:3px solid var(--ink)"></div>
  <div class="photo" style="left:145px;top:675px;width:290px;height:290px" role="img" aria-label="Founder on a phone call"></div>
  <h2 class="section-title" style="left:615px;top:662px;line-height:44px">How We Make Our VC<br>Investments</h2>
  <div class="rule" style="left:615px;top:765px"></div>
  <p class="body-copy" style="left:615px;top:795px;width:470px;font-size:15px;line-height:27px">We follow up on referrals to innovative technology companies at the pre-seed or seed stage of funding. Before meeting, we'll review the company's investor pitch presentation and its website, if we're interested.</p>
  <span class="btn" style="left:615px;top:975px">Read More</span>
</section>

<!-- Portfolio -->
<svg class="abs" style="left:0;top:1080px" width="1200" height="80" viewBox="0 0 1200 80" preserveAspectRatio="none"><path d="M0 40 C300 0 500 80 800 40 C1000 10 1100 30 1200 20 V80 H0Z" fill="#ececec"/></svg>
<section class="grey" style="top:1150px;height:760px">
  <h2 class="section-title" style="left:0;width:1200px;text-align:center;top:80px">Our Portfolio</h2>
  <div class="rule" style="left:565px;top:130px"></div>
  <p class="abs" style="left:0;width:1200px;text-align:center;top:150px;font-size:19px;font-weight:600">Quillbay Fund I Portfolio Companies</p>
  <div class="logo-cell" style="left:110px;top:260px"><span class="sq"></span>Loomtrack</div>
  <div class="logo-cell" style="left:375px;top:260px;color:#8aa;font-size:20px">Vantorel</div>
  <div class="logo-cell" style="left:650px;top:260px">Skorvi</div>
  <div class="logo-cell" style="left:935px;top:260px;font-size:20px">Penlark</div>
  <span class="arrow" style="left:30px;top:410px">&larr;</span>
  <span class="arrow" style="left:1120px;top:410px">&rarr;</span>
  <div class="logo-cell" style="left:110px;top:420px;font-size:20px">Gatewick</div>
  <div class="abs" style="left:340px;top:375px;width:230px;height:130px;background:var(--white);box-shadow:0 4px 14px rgba(0,0,0,.15)"></div>
  <div class="logo-cell" style="left:380px;top:420px;font-size:30px">Orbeta</div>
  <div class="logo-cell" style="left:640px;top:420px;font-size:22px;font-weight:500">Claritune</div>
  <div class="logo-cell" style="left:920px;top:420px;font-size:22px">Opsiven</div>
  <span class="btn" style="left:538px;top:585px">View More</span>
</section>
<svg class="abs" style="left:0;top:1890px" width="1200" height="70" viewBox="0 0 1200 70" preserveAspectRatio="none"><path d="M0 0 H1200 V30 C1000 70 800 0 600 40 C400 70 200 10 0 40Z" fill="#ececec"/></svg>

<!-- Looking for -->
<section>
  <h2 class="section-title" style="left:110px;top:2010px">What We're Looking For</h2>
  <div class="rule" style="left:110px;top:2090px"></div>
  <p class="body-copy" style="left:110px;top:2125px;width:470px;font-size:15px;line-height:27px">We invest in innovative technology companies with these Founding Team: Visionary, Committed, Coachable, Skilled; Total Addressable Market: Large, Growing, and Attractive; Product Market Fit: MVP + Initial Market Validation; Early Revenue and Growth Potential</p>
  <span class="btn" style="left:110px;top:2330px">Read More</span>
  <div class="abs" style="left:665px;top:1985px;width:310px;height:310px;border-radius:50%;border:3px solid var(--ink)"></div>
  <div class="photo" style="left:672px;top:1990px;width:295px;height:295px;background:linear-gradient(160deg,#e8dcc0,#b5a36a)" role="img" aria-label="Entrepreneur working at a laptop"></div>
</section>

<!-- News -->
<svg class="abs" style="left:0;top:2520px" width="1200" height="80" viewBox="0 0 1200 80" preserveAspectRatio="none"><path d="M0 30 C250 80 450 0 700 40 C950 80 1100 20 1200 40 V80 H0Z" fill="#ececec"/></svg>
<section class="grey" style="top:2595px;height:760px">
  <h2 class="section-title" style="left:0;width:1200px;text-align:center;top:115px">Latest News &amp; Blogs</h2>
  <div class="rule" style="left:565px;top:165px"></div>
  <span class="arrow" style="left:30px;top:345px">&larr;</span>
  <span class="arrow" style="left:1120px;top:345px">&rarr;</span>
  <article class="card" style="left:110px;top:185px"><span class="tag">Neque porro quisquam</span><h3>Lorem ipsum dolor sit amet, consectetur adipiscing elit, eiusmo</h3><div class="img" style="background:linear-gradient(135deg,#d8d2c6,#9c8c78)" role="img" aria-label="Person smiling at camera"></div><span class="more">Read More</span></article>
  <article class="card" style="left:445px;top:185px"><span class="tag">Doloriam ipsum quia</span><h3>Sed ut perspiciatis unde omnis iste natus sit voluptatem</h3><div class="img" style="background:linear-gradient(135deg,#4b6a8e,#1f2f46)" role="img" aria-label="Business meeting in an office"></div><span class="more">Read More</span></article>
  <article class="card" style="left:780px;top:178px;box-shadow:0 6px 18px rgba(0,0,0,.2)"><span class="tag">Consectetur, adipisci velit</span><h3>At vero eos et accus et iusto odio dignimos ducimus qui blandit</h3><div class="img" style="background:linear-gradient(135deg,#9fb3c4,#56687a)" role="img" aria-label="City office towers"></div><span class="more" style="color:var(--green)">Read More</span></article>
  <span class="btn" style="left:538px;top:595px">Read More</span>
</section>
<svg class="abs" style="left:0;top:3340px" width="1200" height="60" viewBox="0 0 1200 60" preserveAspectRatio="none"><path d="M0 0 H1200 V20 C900 60 600 10 300 40 C150 55 60 30 0 30Z" fill="#ececec"/></svg>

<!-- Testimonials -->
<section>
  <h2 class="section-title" style="left:0;width:1200px;text-align:center;top:3430px">Testimonials</h2>
  <div class="rule" style="left:565px;top:3480px"></div>
  <div class="abs" style="left:195px;top:3525px;width:170px;height:170px;border-radius:50%;background:var(--green)"></div>
  <div class="abs" style="left:300px;top:3720px;width:110px;height:110px;border-radius:50%;background:#e2e2e2"></div>
  <div class="photo" style="left:235px;top:3565px;width:230px;height:230px;background:linear-gradient(160deg,#d9c5ad,#8a6a4f)" role="img" aria-label="Portrait of a founder"></div>
  <span class="abs" style="left:495px;top:3540px;font-size:80px;color:#bbb;font-weight:700">&ldquo;</span>
  <p class="body-copy" style="left:560px;top:3560px;width:420px;font-size:15px;line-height:26px">Lorem ipsum dolor sit amet, consectetur adipiscing elit, sed do eiusmod tempor incididunt ut labore et dolore magna aliqua. Ut enim ad minim veniam, quis nostrud exercitation ullamco laboris nisi ut aliquip ex ea commodo consequat.</p>
  <span class="abs" style="left:680px;top:3690px;font-size:80px;color:#bbb;font-weight:700">&rdquo;</span>
  <p class="abs" style="left:560px;top:3785px;font-size:28px;font-weight:600">Marla Quennet <span style="font-size:12px;color:#777;font-weight:400">Business</span></p>
  <div class="abs" style="left:1008px;top:3718px;width:42px;height:42px;border-radius:50%;background:var(--green)"></div>
  <svg class="abs" style="left:1018px;top:3728px" width="22" height="22" viewBox="0 0 22 22"><path d="M8 5 L14 11 L8 17" fill="none" stroke="#fff" stroke-width="3"/></svg>
</section>

<!-- Footer -->
<footer class="footer">
  <h4 style="left:110px;top:75px">CONTACT US</h4>
  <div class="rule" style="left:110px;top:105px;width:50px"></div>
  <svg class="abs" style="left:110px;top:125px" width="14" height="18" viewBox="0 0 14 18"><path d="M7 0 C3 0 0 3 0 7 C0 12 7 18 7 18 C7 18 14 12 14 7 C14 3 11 0 7 0Z" fill="#7b9a2f"/><circle cx="7" cy="7" r="2.5" fill="#0d0d0d"/></svg>
  <p class="line" style="left:135px;top:122px;line-height:20px">No. 27 Suite 310,<br>Calgary</p>
  <svg class="abs" style="left:110px;top:180px" width="14" height="14" viewBox="0 0 14 14"><path d="M2 1 L5 1 L6 4 L4 5.5 C5 8 6 9 8.5 10 L10 8 L13 9 L13 12 C13 13 12 13.5 11 13.5 C5 13 1 9 0.5 3 C0.5 2 1 1 2 1Z" fill="#7b9a2f"/></svg>
  <p class="line" style="left:135px;top:178px">555-014-2290</p>
  <svg class="abs" style="left:110px;top:222px" width="15" height="11" viewBox="0 0 15 11"><rect x="0.5" y="0.5" width="14" height="10" fill="none" stroke="#7b9a2f"/><path d="M0.5 0.5 L7.5 6 L14.5 0.5" fill="none" stroke="#7b9a2f"/></svg>
  <p class="line" style="left:135px;top:218px">info@quillbay.vc</p>
  <svg class="abs" style="left:110px;top:260px" width="14" height="14" viewBox="0 0 14 14"><circle cx="7" cy="7" r="6" fill="none" stroke="#7b9a2f" stroke-width="1.5"/><line x1="1" y1="7" x2="13" y2="7" stroke="#7b9a2f"/></svg>
  <p class="line" style="left:135px;top:257px">www.quillbay.vc</p>

  <h4 style="left:352px;top:75px">QUICK LINKS</h4>
  <div class="rule" style="left:352px;top:105px;width:50px"></div>
  <p class="line" style="left:352px;top:122px;line-height:32px">Home<br>What<br>How</p>
  <p class="line" style="left:480px;top:122px;line-height:32px">Portfolio<br>News<br>Contact us</p>
  <span class="social" style="left:352px;top:230px"></span>
  <span class="social" style="left:392px;top:230px"></span>
  <span class="social" style="left:432px;top:230px"></span>
  <span class="social" style="left:472px;top:230px"></span>
  <span class="social" style="left:512px;top:230px"></span>

  <h4 style="left:645px;top:75px">NEWSLETTER</h4>
  <div class="rule" style="left:645px;top:105px;width:50px"></div>
  <div class="abs" style="left:645px;top:127px;width:215px;height:34px;background:var(--white);font-size:11px;color:#999;padding:11px 10px">Enter Your Email</div>
  <span class="abs" style="left:645px;top:178px;background:var(--green);color:#fff;font-size:12px;font-weight:600;padding:8px 14px;border-radius:3px">SUBMIT</span>

  <div class="brand" style="left:925px;top:150px;color:var(--green);font-size:28px"><span class="dot"></span>Quillbay.vc</div>
</footer>
<div class="copy-bar"><p class="abs" style="left:110px;top:22px">Copyright &copy; 2022 Quillbay.vc - All Rights Reserved</p></div>

</body>
</html>
```